Business card

We need a business card design for our company based in Auckland , New Zealand called 'Ridge + Studio Ltd'. We provide architectural services. We would like to see designs that use the max. three colours (such as white, black, grey) The final design should communicate financial safety and growth."
Also I will provide our company logo. I would like to the logo to be embeded onto our business card.

Target Market(s)

new residential house, alteration & addition & light commericila design & drafting service

Industry/Entity Type

Architecture

Contact Information for Business Card

Company name: ridge + studio Ltd.
Name: Mark Delford
Job title: architectural designer & Design LBP
email address: mark@rplusd.co.nz
mobile number: 02 5163 2290
web site: www.rplusd.co.nz

Requirements
Must have
• My project must have..
• - embeded logo (attached company logo)
• I don't have a bigger version for our company logo, but I have one old one, so you can remove the word from it)
• - insert the attached small BKTW logo & LBP logo
• - creative, simple and clear business card.
• - Max. three colours
Nice to have
• - Here are the samples I would like to share with you: http://www.plimvora.com/blog/minimalistic-business-card-designs/
• I would like to have my business card like one of the creation.
Should not have
• TBA

```html
<!DOCTYPE html>
<html lang="en">
<head>
<meta charset="utf-8">
<title>Ridge + Studio Ltd. — Business Card</title>
<link href="https://fonts.googleapis.com/css2?family=Mulish:wght@400;600;700&display=swap" rel="stylesheet">
<style>
  :root {
    --page-bg: #e6e7e8;
    --card-bg: #ffffff;
    --ink: #333333;
    --ink-soft: #3d3d3d;
    --grey: #8c8f8c;
    --rule: #c9c9c9;
    --badge-dark: #3a3a3a;
  }
  * { box-sizing: border-box; margin: 0; padding: 0; }
  html, body {
    width: 1200px; height: 1192px; overflow: hidden;
    background: var(--page-bg);
    font-family: "Mulish", "Helvetica Neue", Arial, sans-serif;
    color: var(--ink);
  }
  .card {
    position: absolute;
    left: 262px; width: 677px; height: 396px;
    background: var(--card-bg);
    border-radius: 16px;
  }
  .card--front { top: 144px; }
  .card--back { top: 621px; }

  .brand-mark {
    position: absolute; left: 268px; top: 168px;
    width: 140px; height: 140px;
    border-radius: 50%;
    background: var(--ink);
    transform: translateY(-0px);
  }
  .front-mark { position: absolute; left: 268px; top: 96px; width: 140px; height: 140px; border-radius: 50%; background: var(--ink); }
  .company-name {
    position: absolute; left: 0; right: 0; top: 260px;
    text-align: center;
    font-size: 32px; font-weight: 700; letter-spacing: -0.5px;
    color: var(--ink);
  }

  .badge-lbp {
    position: absolute; left: 68px; top: 229px;
    width: 92px; height: 92px; border-radius: 50%;
    background: var(--badge-dark);
  }
  .badge-member {
    position: absolute; left: 188px; top: 237px;
    width: 104px; height: 74px;
    background: var(--grey);
  }

  .holder { position: absolute; left: 436px; top: 172px; }
  .holder__name { font-size: 17px; font-weight: 700; color: var(--ink); }
  .holder__title { margin-top: 6px; font-size: 12px; font-weight: 400; color: var(--ink-soft); }
  .holder__rule {
    position: absolute; left: 436px; top: 235px;
    width: 188px; height: 1px; background: var(--rule);
  }
  .contacts { position: absolute; left: 406px; top: 252px; list-style: none; }
  .contacts li {
    display: flex; align-items: center; gap: 10px;
    height: 29px;
    font-size: 17px; font-weight: 400; color: var(--ink-soft);
  }
  .contacts svg { width: 18px; height: 18px; flex: none; }
</style>
</head>
<body>
  <section class="card card--front">
    <div class="front-mark" aria-hidden="true"></div>
    <h1 class="company-name">Ridge + Studio Ltd.</h1>
  </section>

  <section class="card card--back">
    <div class="badge-lbp" role="img" aria-label="Licensed building practitioner badge"></div>
    <div class="badge-member" role="img" aria-label="Professional member badge"></div>

    <div class="holder">
      <p class="holder__name">Mark Delford</p>
      <p class="holder__title">architectural designer &amp; Design LBP</p>
    </div>
    <div class="holder__rule"></div>

    <ul class="contacts">
      <li>
        <svg viewBox="0 0 20 20" aria-hidden="true"><circle cx="10" cy="10" r="8.5" fill="none" stroke="#333" stroke-width="1.3"/><path d="M8 5.5c-1.2.4-1.5 1.6-1.2 3 .4 1.8 1.6 3.6 3.2 4.8.9.7 2 .8 2.6.2l-1.3-1.8-1 .4c-.8-.6-1.4-1.6-1.7-2.6l.8-.6z" fill="#333"/></svg>
        <span>02 5163 2290</span>
      </li>
      <li>
        <svg viewBox="0 0 20 20" aria-hidden="true"><rect x="1.5" y="4" width="17" height="12" fill="#333"/><path d="M1.5 4l8.5 7 8.5-7M1.5 16l6-5.5M18.5 16l-6-5.5" fill="none" stroke="#fff" stroke-width="1.2"/></svg>
        <span>mark@rplusd.co.nz</span>
      </li>
      <li>
        <svg viewBox="0 0 20 20" aria-hidden="true"><g fill="none" stroke="#333" stroke-width="1.3"><circle cx="10" cy="10" r="8"/><ellipse cx="10" cy="10" rx="3.5" ry="8"/><path d="M2 10h16M3.2 6h13.6M3.2 14h13.6"/></g></svg>
        <span>www.rplusd.co.nz</span>
      </li>
    </ul>
  </section>
</body>
</html>
```